Modern Business Card For A Digital Advertising Company

I'll be print on the Pell Prints Velour paper http://us.pellprints.com/products/velour/business-cards.html
Need's to be modern and use the color palette of the logo or gray scales. I think integrating the pixelation of the logo in to the card and having it wrap from one side to the other could be interesting. My company provides ad operations, web development, and number of other services to websites around the world. You can see my website at http://www.zantorhq.com
Contact info on the card needs to have
Owen Lasko
President
p.318.204.6637
owen@zantorhq.com
http://www.zantorhq.com
Doesn't necessarily need to be in that order
Website owners
Business

```html
<!DOCTYPE html>
<html lang="en">
<head>
<meta charset="utf-8">
<title>Zantor HQ — Business Card</title>
<link href="https://fonts.googleapis.com/css2?family=Open+Sans:wght@400;600;700&display=swap" rel="stylesheet">
<style>
  :root {
    --backdrop: #1e1e1e;
    --card-white: #ffffff;
    --green-deep: #5e8a3a;
    --green-bright: #8cc63f;
    --green-logo: #7dba3a;
    --ink-dark: #333333;
    --divider: #2a2a2a;
    --text-light: #ffffff;
  }
  * { box-sizing: border-box; margin: 0; padding: 0; }
  html, body {
    width: 1200px; height: 757px; overflow: hidden;
    background: var(--backdrop);
    font-family: "Open Sans", Arial, sans-serif;
  }
  .stage {
    position: relative; width: 1200px; height: 757px;
    display: flex; align-items: center; justify-content: center; gap: 60px;
  }
  .card {
    width: 500px; height: 286px; border-radius: 22px; overflow: hidden;
    position: relative; box-shadow: 0 10px 30px rgba(0,0,0,.5);
  }
  /* Front */
  .card-front { display: flex; background: var(--card-white); }
  .front-brand {
    width: 47%; display: flex; align-items: center; justify-content: center; gap: 10px;
  }
  .brand-square { width: 22px; height: 22px; background: var(--green-logo); }
  .brand-name {
    font-weight: 700; font-size: 30px; color: var(--green-logo); letter-spacing: 1px;
  }
  .front-divider { width: 3px; background: var(--divider); }
  .front-contact {
    flex: 1; color: var(--text-light); padding: 50px 0 0 30px;
    background: linear-gradient(160deg, var(--green-deep) 0%, var(--green-bright) 100%);
  }
  .contact-name { font-weight: 700; font-size: 19px; letter-spacing: .3px; }
  .contact-title { font-size: 12px; margin-bottom: 22px; }
  .contact-list { list-style: none; font-size: 12.5px; line-height: 1.55; }
  .contact-list li { display: flex; align-items: center; gap: 8px; }
  .contact-list svg { width: 10px; height: 10px; fill: var(--text-light); flex: none; }
  /* Back */
  .card-back {
    background: linear-gradient(160deg, var(--green-deep) 0%, var(--green-bright) 100%);
    display: flex; flex-direction: column; align-items: center; justify-content: center;
    color: var(--text-light);
  }
  .back-brand { display: flex; align-items: center; gap: 14px; margin-bottom: 40px; }
  .back-brand .brand-square { width: 34px; height: 34px; background: var(--text-light); }
  .back-brand .brand-name { color: var(--text-light); font-size: 46px; }
  .back-url { font-weight: 700; font-size: 19px; letter-spacing: 1.5px; }
</style>
</head>
<body>
<main class="stage">
  <section class="card card-front" aria-label="Card front">
    <div class="front-brand">
      <span class="brand-square"></span>
      <span class="brand-name">ZANTOR HQ</span>
    </div>
    <div class="front-divider"></div>
    <div class="front-contact">
      <h1 class="contact-name">OWEN LASKO</h1>
      <p class="contact-title">President</p>
      <ul class="contact-list">
        <li><svg viewBox="0 0 10 10"><path d="M2 0h2l1 3-1.5 1a6 6 0 0 0 2.5 2.5L7 5l3 1v2a2 2 0 0 1-2 2C4 10 0 6 0 2a2 2 0 0 1 2-2z"/></svg>318.204.6637</li>
        <li><svg viewBox="0 0 10 10"><path d="M0 2h10v6H0z M0 2l5 3.5L10 2" stroke="#5e8a3a" stroke-width=".8"/></svg>owen@zantorhq.com</li>
        <li><svg viewBox="0 0 10 10"><circle cx="5" cy="5" r="5"/><path d="M0 5h10M5 0v10" stroke="#5e8a3a" stroke-width=".7"/></svg>www.zantorhq.com</li>
      </ul>
    </div>
  </section>

  <section class="card card-back" aria-label="Card back">
    <div class="back-brand">
      <span class="brand-square"></span>
      <span class="brand-name">ZANTOR HQ</span>
    </div>
    <p class="back-url">www.zantorhq.com</p>
  </section>
</main>
</body>
</html>
```